Volunteer fire fighters needed banner

As part of our recruitment campaign, we need a sign we can post on our sign trailer to entice locals to join our volunteer fire service. This design will be printed on a banner, front and back, to catch traffic going in both directions on a busy roadway. This banner will have a printed surface of 4 feet tall by 8 feet long.
Our fire department is looking to attract people between the ages of 18 and 35 years old who are interested in being a firefighter. We offer our volunteers:
-Free professional training
-All equipment supplied
-Tax abatements for active volunteers
For more information, you can check us out at:
Brackenmoorfire.example

This design should:
-scale to and fit a 4'x8' canvas
-Include our web address "BrackenMoorFire.example"
-Say "Members Wanted"
-"Drill every Tuesday at 7pm"
-"57 Kestrel Pond Lane"
-Include "Bracken Moor Fire Department"

We've included reference photos and past images we use for our other campaigns for inspiration for you.

Target Market(s)

18-35 y/o

Industry/Entity Type

Fire Service

Requirements
Must have
• -scale to and fit a 4'x8' canvas -Include our web address "BrackenMoorFire.example" -Say "Members Wanted" -"Drill every Tuesday at 7pm" -"57 Kestrel Pond Lane" -Include "Bracken Moor Fire Department"

```html
<!DOCTYPE html>
<html lang="en">
<head>
<meta charset="utf-8">
<title>Members Wanted – Bracken Moor Fire Department</title>
<link rel="stylesheet" href="https://fonts.googleapis.com/css2?family=Alfa+Slab+One&family=Archivo+Black&family=Montserrat:wght@700&display=swap">
<style>
  :root {
    --sky: #8fd0e6;
    --teal: #4aa3a8;
    --ember: #d9512b;
    --truck-red: #b8322a;
    --gold-light: #fff27a;
    --gold: #f5b60f;
    --gold-deep: #e0700a;
    --fire-red: #e3120b;
    --shadow-red: #9c0d06;
    --navy: #1c2757;
    --white: #ffffff;
    --ink: #111111;
  }
  * { margin: 0; padding: 0; box-sizing: border-box; }
  html, body { width: 1200px; height: 600px; overflow: hidden; background: #ffffff; }
  .banner {
    position: relative;
    width: 1200px;
    height: 600px;
    overflow: hidden;
    font-family: "Archivo Black", sans-serif;
  }
  .photo-collage {
    position: absolute;
    inset: 0 0 80px 0;
    background:
      radial-gradient(ellipse at 58% 45%, rgba(255,230,90,0.55), transparent 40%),
      radial-gradient(ellipse at 20% 75%, rgba(217,81,43,0.7), transparent 45%),
      radial-gradient(ellipse at 75% 15%, rgba(184,50,42,0.55), transparent 35%),
      linear-gradient(160deg, var(--sky) 0%, var(--teal) 55%, #3e7f8f 100%);
  }
  .bottom-band {
    position: absolute;
    left: 0; right: 0; bottom: 0;
    height: 81px;
    background: var(--navy);
  }
  .headline {
    position: absolute;
    left: 0; right: 0;
    text-align: center;
    font-family: "Alfa Slab One", serif;
    text-transform: uppercase;
    line-height: 1;
    white-space: nowrap;
  }
  .headline span {
    background: linear-gradient(180deg, var(--gold-light) 0%, var(--gold) 45%, var(--gold-deep) 100%);
    -webkit-background-clip: text;
    background-clip: text;
    color: transparent;
    filter: drop-shadow(1px 1px 0 var(--fire-red)) drop-shadow(2px 2px 0 var(--fire-red)) drop-shadow(3px 3px 0 var(--shadow-red)) drop-shadow(4px 4px 0 var(--shadow-red));
  }
  .headline-members { top: 84px; font-size: 76px; letter-spacing: 1px; padding-left: 0; transform: translateX(-25px); }
  .headline-drill { top: 178px; font-size: 84px; letter-spacing: 1px; transform: translateX(-30px); }
  .drill-time {
    position: absolute;
    top: 290px; left: 0; right: 0;
    text-align: center;
    font-size: 72px;
    color: var(--white);
    -webkit-text-stroke: 3px var(--ink);
    paint-order: stroke fill;
    transform: translateX(-6px);
  }
  .address {
    position: absolute;
    top: 404px; left: 0; right: 0;
    text-align: center;
    font-size: 50px;
    color: var(--fire-red);
    -webkit-text-stroke: 3px var(--white);
    paint-order: stroke fill;
    transform: translateX(-4px);
  }
  .web-address {
    position: absolute;
    bottom: 14px; left: 0; right: 0;
    text-align: center;
    font-family: "Montserrat", sans-serif;
    font-weight: 700;
    font-size: 48px;
    color: var(--white);
    transform: translateX(-6px);
  }
  .dept-name, .event-name {
    position: absolute;
    display: flex;
    flex-direction: column;
    align-items: center;
    justify-content: center;
    text-align: center;
    gap: 10px;
    font-family: "Archivo Black", sans-serif;
    color: var(--white);
    line-height: 1.1;
    text-transform: uppercase;
  }
  .dept-name { left: 40px; top: 340px; width: 190px; height: 215px; font-size: 24px; }
  .event-name { left: 955px; top: 300px; width: 215px; height: 270px; font-size: 24px; }
  .name-dot { width: 34px; height: 34px; border-radius: 50%; background: var(--fire-red); }
</style>
</head>
<body>
<main class="banner">
  <div class="photo-collage" role="img" aria-label="Collage of volunteer firefighters in gear, red fire engines and the station bay"></div>
  <div class="bottom-band"></div>

  <h1 class="headline headline-members"><span>Members Wanted</span></h1>
  <p class="headline headline-drill"><span>Drill Every Tuesday</span></p>
  <p class="drill-time">aT 7:00 PM</p>
  <p class="address">57 Kestrel Pond Lane</p>

  <div class="dept-name">
    <span class="name-dot"></span>
    <span>Bracken Moor Fire Department</span>
  </div>

  <div class="event-name">
    <span class="name-dot"></span>
    <span>Ada Marsh Memorial Egg Hunt</span>
  </div>

  <p class="web-address">BrackenMoorFire.example</p>
</main>
</body>
</html>
```